New Website

New website is to be the same as Amber Lantern.

Website needs to be fully functional, with only text and logo to be added by client at a later date.

Logo has been added for reference.

```html
<!DOCTYPE html>
<html lang="en">
<head>
<meta charset="utf-8">
<title>Velora – Consulting Made Simple</title>
<link rel="stylesheet" href="https://fonts.googleapis.com/css2?family=Oswald:wght@400;500&family=Open+Sans:wght@400;600;700&display=swap">
<style>
:root{
  --blue:#1f86cc;
  --blue-dark:#176ca8;
  --navy:#2f4a9b;
  --ink:#222;
  --text:#333;
  --muted:#777;
  --light:#d9d9d9;
  --white:#fff;
  --footer:#2a2a2a;
  --footer-bottom:#1e1e1e;
  --footer-text:#9a9a9a;
}
*{margin:0;padding:0;box-sizing:border-box}
html,body{width:1200px;height:2276px;overflow:hidden}
body{position:relative;background:var(--white);font-family:"Open Sans",Arial,sans-serif;color:var(--text)}
.abs{position:absolute}
.heading{font-family:"Oswald","Arial Narrow",sans-serif;font-weight:400;color:var(--ink);text-transform:uppercase}

/* header */
.site-header{position:absolute;left:0;top:0;width:1200px;height:128px;background:var(--white)}
.brand-mark{position:absolute;left:105px;top:22px;width:88px;height:88px;border-radius:50%;background:var(--navy)}
.brand-name{position:absolute;left:220px;top:38px;font-size:40px;font-weight:600;color:var(--navy);letter-spacing:1px;line-height:1}
.brand-tag{position:absolute;left:222px;top:86px;font-size:15px;color:#4a9bd6;white-space:nowrap}
.nav a{position:absolute;top:69px;font-size:12px;font-weight:600;color:var(--ink);text-decoration:none;text-transform:uppercase}
.nav a.active{color:var(--blue)}
.btn-outline{position:absolute;top:61px;left:893px;width:77px;height:29px;border:1px solid var(--blue);border-radius:2px;font-size:12px;text-align:center;line-height:27px;color:var(--ink)}
.btn-solid{position:absolute;top:61px;left:997px;width:77px;height:29px;background:var(--blue);border-radius:2px;font-size:12px;text-align:center;line-height:29px;color:var(--white)}

/* hero */
.hero{position:absolute;left:0;top:128px;width:1200px;height:515px}
.hero-photo{position:absolute;inset:0;background:linear-gradient(90deg,#3f4650 0%,#6b7480 40%,#9aa2aa 70%,#c8ccd0 100%)}
.finder{position:absolute;right:0;top:0;width:305px;height:47px;background:var(--blue);clip-path:polygon(12px 0,100% 0,100% 100%,0 100%);color:var(--white);font-size:13px;font-weight:600;padding:15px 0 0 60px}
.hero-kicker{position:absolute;left:118px;top:163px;font-size:23px;line-height:1.2;color:var(--white);font-family:"Oswald",sans-serif;text-transform:uppercase}
.hero-title{position:absolute;left:118px;top:196px;font-size:34px;line-height:1.2;font-weight:500;color:var(--white);font-family:"Oswald",sans-serif;text-transform:uppercase;white-space:nowrap}
.hero-copy{position:absolute;left:118px;top:252px;font-size:16px;line-height:26px;color:var(--white);white-space:nowrap}
.hero-btn{position:absolute;left:118px;top:328px;width:277px;height:44px;background:var(--blue);border-radius:3px;color:var(--white);font-size:13px;font-weight:600;line-height:44px;padding-left:50px}
.dot{position:absolute;width:13px;height:13px;border-radius:50%;border:2px solid var(--blue)}
.dot.on{background:var(--blue)}

/* services */
.services-title{position:absolute;top:686px;width:1200px;text-align:center;font-size:24px}
.services-sub{position:absolute;top:740px;width:1200px;text-align:center;font-size:12px;text-transform:uppercase;color:var(--text)}
.service{position:absolute;top:802px;width:240px;text-align:center}
.service-icon{display:block;margin:0 auto;width:106px;height:106px;border-radius:50%;background:var(--blue)}
.service-shadow{display:block;margin:10px auto 0;width:100px;height:10px;border-radius:50%;background:#ddd}
.service h3{margin-top:16px;font-size:17px}
.service p{margin-top:10px;font-size:12px;line-height:24px;color:var(--text)}

/* newsletter */
.newsletter{position:absolute;left:0;top:1097px;width:1200px;height:177px;background:#5b5b5b}
.newsletter-photo{position:absolute;left:99px;top:0;width:1002px;height:177px;background:linear-gradient(90deg,#4b4b4b,#8a8a8a 55%,#6e6e6e)}
.newsletter h2{position:absolute;left:130px;top:68px;font-size:17px;color:var(--white)}
.newsletter small{position:absolute;left:130px;top:93px;font-size:11px;color:#eee}
.field{position:absolute;height:41px;background:var(--white);border:1px solid #ccc;font-size:11px;color:#999;padding:12px 0 0 10px}
.newsletter .submit{position:absolute;left:858px;top:68px;width:137px;height:41px;background:var(--blue);color:var(--white);font-family:"Oswald",sans-serif;font-size:14px;text-align:center;line-height:41px;text-transform:uppercase}

/* latest */
.latest{position:absolute;left:0;top:1274px;width:1200px;height:364px;background:var(--light)}
.latest h2{position:absolute;font-size:23px}
.ph{position:absolute}
.video-photo{left:99px;top:89px;width:271px;height:230px;background:linear-gradient(135deg,#c9d6e2,#8ea4b8 60%,#51616f)}
.video-bar{position:absolute;left:99px;top:308px;width:271px;height:11px;background:#222}
.video-title{position:absolute;left:388px;top:84px;font-size:16px;font-weight:400;line-height:21px;color:var(--ink);text-transform:uppercase;white-space:nowrap}
.video-date{position:absolute;left:392px;top:133px;font-size:11px;font-weight:700}
.video-copy{position:absolute;left:392px;top:156px;width:215px;font-size:12px;line-height:24px}
.btn-more{position:absolute;left:388px;top:291px;width:107px;height:31px;background:#39a0e6;color:var(--white);font-size:12px;text-align:center;line-height:31px}
.news-photo{width:125px;height:94px;left:644px;background:linear-gradient(135deg,#e8edf2,#b6c1cb)}
.news-item{position:absolute;left:788px;width:260px}
.news-item h4{font-size:12px;font-weight:700;line-height:21px;text-transform:uppercase;color:var(--ink);white-space:nowrap}
.news-item p{margin-top:4px;font-size:11.5px;line-height:19px;color:#444}

/* testimonials */
.clients-title{position:absolute;top:1654px;width:1200px;text-align:center;font-size:21px}
.client-photo{position:absolute;left:183px;top:1695px;width:130px;height:130px;border-radius:50%;background:linear-gradient(160deg,#d7dde2,#7a8794)}
.quote{position:absolute;left:338px;top:1707px;width:625px;font-size:11.5px;line-height:24px;color:var(--ink)}
.quote-by{position:absolute;left:338px;top:1785px;font-size:12px}
.quote-by b{color:var(--blue)}
.sdot{position:absolute;top:1825px;width:10px;height:10px;border-radius:50%;background:#999}
.sdot.on{background:var(--blue)}

/* footer */
.footer{position:absolute;left:0;top:1864px;width:1200px;height:301px;background:var(--footer)}
.f-mark{position:absolute;left:95px;top:14px;width:55px;height:55px;border-radius:50%;background:var(--navy)}
.f-name{position:absolute;left:170px;top:22px;font-size:26px;font-weight:600;color:#5a78c8;line-height:1}
.f-tag{position:absolute;left:163px;top:54px;font-size:10px;color:#4a9bd6;white-space:nowrap}
.f-about{position:absolute;left:97px;top:86px;width:210px;font-size:11px;font-weight:700;line-height:21px;color:var(--footer-text)}
.footer h5{position:absolute;top:46px;font-family:"Oswald",sans-serif;font-weight:400;font-size:16px;color:#ddd;text-transform:uppercase}
.f-thumb{position:absolute;left:352px;width:78px;height:71px;background:linear-gradient(135deg,#cfd8e0,#7d8a96)}
.f-event{position:absolute;left:444px;width:170px;font-size:11.5px;line-height:20px;color:var(--footer-text)}
.f-event .t{text-transform:uppercase;color:#888}
.f-event .d{color:var(--blue)}
.contact{position:absolute;left:657px;font-size:11.5px;color:var(--footer-text)}
.contact svg{vertical-align:middle;margin-right:8px}
.f-signup{position:absolute;left:893px;top:88px;width:210px;font-size:11.5px;line-height:21px;color:var(--footer-text)}
.f-field{position:absolute;left:893px;width:207px;height:29px;background:#f6f6f6;border-radius:2px;font-size:12px;color:#888;padding:6px 0 0 14px}
.f-login{position:absolute;left:893px;top:226px;width:87px;height:29px;background:var(--blue);border-radius:2px;color:var(--white);font-size:12px;font-weight:600;text-align:center;line-height:29px}
.footer-bottom{position:absolute;left:0;top:2165px;width:1200px;height:111px;background:var(--footer-bottom)}
.legal{position:absolute;left:98px;top:21px;font-size:11px;color:#aaa}
.social{position:absolute;top:50px;width:22px;height:22px;border-radius:50%;border:1px solid #888}
.copyright{position:absolute;right:98px;top:47px;font-size:11px;color:#aaa}
</style>
</head>
<body>

<header class="site-header">
  <span class="brand-mark"></span>
  <span class="brand-name">VELORA</span>
  <span class="brand-tag">pathways to steady progress</span>
  <nav class="nav">
    <a class="active" style="left:513px">How it works</a>
    <a style="left:642px">Products</a>
    <a style="left:747px">Blog</a>
    <a style="left:826px">Help</a>
  </nav>
  <span class="btn-outline">SIGN IN</span>
  <span class="btn-solid">REGISTER</span>
</header>

<section class="hero">
  <div class="hero-photo" role="img" aria-label="Smiling businessman in a suit standing in a bright office"></div>
  <div class="finder">FIND YOUR EXPERT
    <svg class="abs" style="left:20px;top:17px" width="28" height="12" viewBox="0 0 28 12"><circle cx="7" cy="6" r="5" fill="none" stroke="#fff" stroke-width="2"/><circle cx="21" cy="6" r="5" fill="none" stroke="#fff" stroke-width="2"/><path d="M12 6h4" stroke="#fff" stroke-width="2"/></svg>
    <svg class="abs" style="left:183px;top:20px" width="12" height="7" viewBox="0 0 12 7"><path d="M0 0h12L6 7z" fill="#fff"/></svg>
  </div>
  <div class="hero-kicker">Consulting made simple</div>
  <div class="hero-title">The right advisor, right away</div>
  <p class="hero-copy">Lorem Ipsum has been the industry's standard dummy text<br>ever since the 1500s, when an unknown printer took a</p>
  <div class="hero-btn">BROWSE BUSINESS CATEGORIES &gt;&gt;
    <svg class="abs" style="left:14px;top:16px" width="28" height="12" viewBox="0 0 28 12"><circle cx="7" cy="6" r="5" fill="none" stroke="#fff" stroke-width="2"/><circle cx="21" cy="6" r="5" fill="none" stroke="#fff" stroke-width="2"/><path d="M12 6h4" stroke="#fff" stroke-width="2"/></svg>
  </div>
  <span class="dot" style="left:118px;top:452px"></span>
  <span class="dot on" style="left:139px;top:452px"></span>
  <span class="dot" style="left:160px;top:452px"></span>
</section>

<h2 class="heading services-title">Our services</h2>
<p class="services-sub">Find an expert who's just right for your business need. Your expert package includes:</p>

<div class="service" style="left:99px">
  <svg class="service-icon" viewBox="0 0 106 106"><circle cx="53" cy="53" r="53" fill="#1f86cc"/><path d="M32 52 76 34 62 76 53 60z M53 60 76 34" fill="none" stroke="#fff" stroke-width="3" stroke-linejoin="round"/></svg>
  <span class="service-shadow"></span>
  <h3 class="heading">Pre-session discovery</h3>
  <p>payFlux will pay the seller within 24 hours on B2B ecommerce website sales, statement and credit processing.</p>
</div>
<div class="service" style="left:340px">
  <svg class="service-icon" viewBox="0 0 106 106"><circle cx="53" cy="53" r="53" fill="#1f86cc"/><rect x="33" y="35" width="40" height="28" rx="2" fill="#fff"/><rect x="37" y="39" width="32" height="20" fill="#1f86cc"/><circle cx="53" cy="46" r="4" fill="#fff"/><path d="M45 58a8 7 0 0 1 16 0z" fill="#fff"/><path d="M47 70h12M53 63v7" stroke="#fff" stroke-width="3"/></svg>
  <span class="service-shadow"></span>
  <h3 class="heading">One-on-one session</h3>
  <p>payFlux will pay the seller within 24 hours on B2B ecommerce website sales, statement and credit processing.</p>
</div>
<div class="service" style="left:600px">
  <svg class="service-icon" viewBox="0 0 106 106"><circle cx="53" cy="53" r="53" fill="#1f86cc"/><rect x="38" y="32" width="32" height="42" rx="2" fill="none" stroke="#fff" stroke-width="3"/><path d="M45 42h18M45 49h18M45 56h18M45 63h18" stroke="#fff" stroke-width="2.5"/><path d="M35 38h6M35 48h6M35 58h6M35 68h6" stroke="#fff" stroke-width="2.5"/></svg>
  <span class="service-shadow"></span>
  <h3 class="heading">Session summary report</h3>
  <p>payFlux will pay the seller within 24 hours on B2B ecommerce website sales, statement and credit processing.</p>
</div>
<div class="service" style="left:857px">
  <svg class="service-icon" viewBox="0 0 106 106"><circle cx="53" cy="53" r="53" fill="#1f86cc"/><path d="M53 30a13 13 0 0 0-8 23v7h16v-7a13 13 0 0 0-8-23z" fill="none" stroke="#fff" stroke-width="3"/><path d="M46 66h14M48 72h10" stroke="#fff" stroke-width="3"/></svg>
  <span class="service-shadow"></span>
  <h3 class="heading">Post-session options</h3>
  <p>payFlux will pay the seller within 24 hours on B2B ecommerce website sales, statement and credit processing.</p>
</div>

<section class="newsletter">
  <div class="newsletter-photo" role="img" aria-label="Hands typing on a keyboard beside printed financial charts"></div>
  <h2 class="heading">Subscribe to newsletters</h2>
  <small>In dolor eros, mollis non convallis</small>
  <div class="field" style="left:360px;top:68px;width:216px">Name</div>
  <div class="field" style="left:608px;top:68px;width:217px">Email</div>
  <div class="submit">Subscribe</div>
</section>

<section class="latest">
  <h2 class="heading" style="left:99px;top:36px">Latest videos</h2>
  <div class="ph video-photo" role="img" aria-label="Video still of colleagues talking at a meeting table"></div>
  <div class="video-bar"><span class="abs" style="left:18px;top:4px;width:200px;height:3px;background:#3a8fd0"></span></div>
  <h3 class="video-title">Prestige buildings and<br>long island estate homes</h3>
  <div class="video-date">MARCH 26, 2014</div>
  <p class="video-copy">Lorem Ipsum is simply dummy text of the printing and typesetting industry. Lorem Ipsum has been the industry's standard dummy text ever since the 1500s</p>
  <div class="btn-more">View More</div>

  <h2 class="heading" style="left:642px;top:38px">Latest news</h2>
  <div class="ph news-photo" style="top:89px" role="img" aria-label="Two colleagues working at a laptop"></div>
  <div class="news-item" style="top:85px">
    <h4>Vulputate libero a justo posuere,<br>ac ullamcorper sem imperdiet.</h4>
    <p>Nunc accumsan orci ac justo sollicitudin, ullam-corper porttitor nulla vestibulum. Praesent pel-lentesque, erat vel aliquet vehicula,</p>
  </div>
  <div class="ph news-photo" style="top:210px" role="img" aria-label="Businesswoman smiling at her desk"></div>
  <div class="news-item" style="top:208px">
    <h4>Vulputate libero a justo posuere,<br>ac ullamcorper sem imperdiet.</h4>
    <p>Nunc accumsan orci ac justo sollicitudin, ullam-corper porttitor nulla vestibulum. Praesent pel-lentesque, erat vel aliquet vehicula,</p>
  </div>
</section>

<h2 class="heading clients-title">What our clients say</h2>
<div class="client-photo" role="img" aria-label="Portrait of a client in a suit"></div>
<p class="quote">Sed sit amet commodo nunc, in iaculis nisl. Vivamus id ullamcorper elit, id semper magna. Morbi dapibus turpis sed malesuada laoreet. Cras molestie neque nec urna volutpat, in facilisis justo fermentum. Quisque sapien mauris, pulvinar in congue sit amet, mattis eget ligula. Mauris a molestie odio</p>
<p class="quote-by"><b>- Jane Doe</b>, lorem ipsum</p>
<span class="sdot" style="left:578px"></span>
<span class="sdot on" style="left:595px"></span>
<span class="sdot" style="left:612px"></span>

<footer class="footer">
  <span class="f-mark"></span>
  <span class="f-name">VELORA</span>
  <span class="f-tag">pathways to steady progress</span>
  <p class="f-about">It is a long established fact that a reader will be distracted by the read-able content of a page when looking at its layout. The point of using Lorem Ipsum is that it has a more-or-less normal distribution of letters.</p>

  <h5 style="left:352px">News &amp; Events</h5>
  <div class="f-thumb" style="top:92px" role="img" aria-label="Laptop on a desk"></div>
  <div class="f-event" style="top:92px"><div class="t">Sed a condimentum eros.</div><div class="d">20/08/13</div><div>Duis fringilla nibh at aliquam dignissim. Nulla erat nulla,</div></div>
  <div class="f-thumb" style="top:186px" role="img" aria-label="Businessman holding a tablet"></div>
  <div class="f-event" style="top:186px"><div class="t">Sed a condimentum eros.</div><div class="d">20/08/13</div><div>Duis fringilla nibh at aliquam dignissim. Nulla erat nulla,</div></div>

  <h5 style="left:657px">News &amp; Events</h5>
  <div class="contact" style="top:92px"><svg width="12" height="12" viewBox="0 0 12 12"><path d="M6 1 0 6h2v5h3V8h2v3h3V6h2z" fill="#bbb"/></svg>Address: 123 Street, City, Country</div>
  <div class="contact" style="top:133px"><svg width="12" height="12" viewBox="0 0 12 12"><path d="M2 0 4 2 3 4c1 2 3 4 5 5l2-1 2 2-2 2C5 12 0 7 0 2z" fill="#bbb"/></svg>Phone: (123) 456-7890</div>
  <div class="contact" style="top:174px"><svg width="12" height="12" viewBox="0 0 12 12"><rect x="0" y="4" width="12" height="7" fill="#bbb"/><rect x="3" y="0" width="6" height="4" fill="#bbb"/></svg>Fax: (123) 456-7890</div>
  <div class="contact" style="top:215px"><svg width="12" height="10" viewBox="0 0 12 10"><rect width="12" height="10" fill="#bbb"/><path d="M0 0l6 5 6-5" fill="none" stroke="#2a2a2a"/></svg>Email: info@yoursite.com</div>

  <h5 style="left:893px">News &amp; Events</h5>
  <p class="f-signup">Sign up for our newsletter and get the latest news.</p>
  <div class="f-field" style="top:146px">User name</div>
  <div class="f-field" style="top:186px">Password</div>
  <div class="f-login">Login</div>
</footer>

<div class="footer-bottom">
  <div class="legal">Privacy Policy | &nbsp; Store Locator | &nbsp; Advanced Search | &nbsp; Terms &amp; Conditions</div>
  <span class="social" style="left:98px"></span>
  <span class="social" style="left:125px"></span>
  <span class="social" style="left:152px"></span>
  <span class="social" style="left:179px"></span>
  <span class="social" style="left:206px"></span>
  <div class="copyright">Copyright © &nbsp;Velora pathways to steady progress 2014. All Rights Reserved</div>
</div>

</body>
</html>
```